Upmarket Dessert Lounge needs a Business Card Design

We are an upmarket dessert lounge needing a business card to match our image.

We want something that is simple yet beautiful, feminine, classy, sophisticated and elegant. We want it to stand out and don't mind if it is bold.

The design should include our logo and colours of red or maroon with gold highlights. We don't mind if black is used.

Marlow & Quince

Target Market(s)

For those who like to indulge or treat themselves and give in to their temptations on good quality desserts.

Industry/Entity Type

Business

Requirements
Must have
• Must include our logo and our name

Marlow & Quince

M & Q

```html
<!DOCTYPE html>
<html lang="en">
<head>
<meta charset="utf-8">
<title>Marlow &amp; Quince — Business Card</title>
<link rel="stylesheet" href="https://fonts.googleapis.com/css2?family=Source+Sans+3:wght@400;600;700&display=swap">
<style>
  :root {
    --backdrop: #e8e3dd;
    --card: #2a2526;
    --maroon: #7a1416;
    --cream: #f7d9a8;
    --divider: #6b5f58;
  }
  * { margin: 0; padding: 0; box-sizing: border-box; }
  html, body { width: 1200px; height: 402px; overflow: hidden; }
  body {
    background: var(--backdrop);
    position: relative;
    font-family: "Source Sans 3", Arial, sans-serif;
    color: var(--cream);
  }
  .card {
    position: absolute;
    top: 56px;
    width: 512px;
    height: 292px;
    border-radius: 16px;
    background: var(--card);
    overflow: hidden;
  }
  .card--front { left: 65px; }
  .card--back { left: 627px; }

  .brand-name {
    position: absolute;
    left: 30px;
    top: 106px;
    width: 220px;
    text-align: center;
    font-weight: 600;
    font-size: 21px;
    letter-spacing: 1px;
    line-height: 32px;
    text-transform: uppercase;
    color: var(--cream);
  }
  .divider {
    position: absolute;
    left: 270px;
    top: 46px;
    width: 1px;
    height: 153px;
    background: var(--divider);
  }
  .address {
    position: absolute;
    left: 294px;
    top: 60px;
    font-size: 13.5px;
    line-height: 15px;
  }
  .contact-list {
    position: absolute;
    left: 294px;
    top: 120px;
    list-style: none;
    font-size: 13.5px;
  }
  .contact-list li {
    display: flex;
    align-items: center;
    gap: 5px;
    height: 17.5px;
  }
  .contact-list svg { width: 10px; height: 10px; fill: var(--cream); flex: none; }

  .footer-bands { position: absolute; left: 0; top: 0; width: 512px; height: 292px; }
  .holder-name {
    position: absolute;
    left: 331px;
    top: 252px;
    font-size: 15.5px;
    font-weight: 700;
  }
  .holder-name .title { font-weight: 400; font-size: 14px; }

  .monogram {
    position: absolute;
    inset: 0;
    display: flex;
    align-items: center;
    justify-content: center;
    font-weight: 600;
    font-size: 78px;
    letter-spacing: 2px;
    color: var(--cream);
  }
</style>
</head>
<body>
  <section class="card card--front" aria-label="Card front">
    <div class="brand-name">Marlow &amp; Quince</div>
    <div class="divider"></div>
    <p class="address">Street Name, City Name<br>State Zip Code</p>
    <ul class="contact-list">
      <li><svg viewBox="0 0 10 10"><path d="M2 0.5l2 2-1 1.2c.6 1.3 1.6 2.3 2.9 2.9l1.2-1 2 2-1.2 1.9C4.5 9.5.5 5.5.1 1.7z"/></svg>555-014-2270</li>
      <li><svg viewBox="0 0 10 10"><path d="M3 0h4a1 1 0 0 1 1 1v8a1 1 0 0 1-1 1H3a1 1 0 0 1-1-1V1a1 1 0 0 1 1-1zm.6 1.4v5.4h2.8V1.4z"/></svg>555-014-2270</li>
      <li><svg viewBox="0 0 10 10"><path d="M0 2h10v.8L5 5.8 0 2.8zm0 2l5 3 5-3V8H0z"/></svg>info@marlowquince.com</li>
      <li><svg viewBox="0 0 10 10"><path d="M5 0a5 5 0 1 0 0 10A5 5 0 0 0 5 0zm-.5 1.1v1.7H3.1c.3-.9.8-1.5 1.4-1.7zm1 0c.6.2 1.1.8 1.4 1.7H5.5zM2.1 2.8H1.5a4 4 0 0 1 1.3-1.3 4 4 0 0 0-.7 1.3zm5.8 0a4 4 0 0 0-.7-1.3 4 4 0 0 1 1.3 1.3zM1.1 3.8h1.8a8 8 0 0 0 0 2.4H1.1a4 4 0 0 1 0-2.4zm2.8 0h.6v2.4h-.6a7 7 0 0 1 0-2.4zm1.6 0h.6a7 7 0 0 1 0 2.4h-.6zm1.6 0h1.8a4 4 0 0 1 0 2.4H7.1a8 8 0 0 0 0-2.4zM1.5 7.2h.6a4 4 0 0 0 .7 1.3 4 4 0 0 1-1.3-1.3zm1.6 0h1.4v1.7c-.6-.2-1.1-.8-1.4-1.7zm2.4 0h1.4c-.3.9-.8 1.5-1.4 1.7zm2.4 0h.6a4 4 0 0 1-1.3 1.3 4 4 0 0 0 .7-1.3z"/></svg>www.marlowquince.com</li>
    </ul>
    <svg class="footer-bands" viewBox="0 0 512 292" aria-hidden="true">
      <polygon points="0,252 284,252 271,265 0,265" fill="var(--cream)"/>
      <polygon points="0,268 276,268 297,245 512,245 512,292 0,292" fill="var(--maroon)"/>
    </svg>
    <p class="holder-name">Your name, <span class="title">Title</span></p>
  </section>

  <section class="card card--back" aria-label="Card back">
    <div class="monogram">M &amp; Q</div>
  </section>
</body>
</html>
```